Custom Manufacturing Company square space website design

I own a custom manufacturing company that uses precision cutting technology to manufacture project components over a couple industries. We have an industrial CNC router and state of the art edge bander and cut a lot of cabinetry components for cabinet shops, builders, closet companies, ect. We offer design and assembly for any cabinetry or can build cabinets to spec. We also cut components for other industries out of wood, plastics, acryclics, ect. We offer design engineering services, product development protype services. we have a 3D printer farm. We want our communicate trust, dependability, and the value we place on client relationships.

We essentially want a credibility website. Landing page and drops downs for services we offer, capabilites, about us, contact

```html
<!DOCTYPE html>
<html lang="en">
<head>
<meta charset="utf-8">
<title>Northfield Router Works</title>
<link href="https://fonts.googleapis.com/css2?family=Michroma&family=Lato:wght@400;700&display=swap" rel="stylesheet">
<style>
:root{
  --ink:#111111;
  --dark:#161616;
  --white:#ffffff;
  --band:#f3f3f3;
  --muted:#444444;
  --line:#cfcfcf;
  --frame:#c9c9c9;
  --input:#f4f4f4;
}
*{margin:0;padding:0;box-sizing:border-box}
html,body{width:1200px;height:3969px;overflow:hidden;background:var(--white)}
body{position:relative;font-family:'Lato',sans-serif;color:var(--ink)}
.abs{position:absolute}
.display{font-family:'Michroma',sans-serif;text-transform:uppercase;color:var(--ink)}
.photo{position:absolute}

/* header */
.brand{left:108px;top:40px;display:flex;align-items:center;gap:12px}
.brand-mark{width:26px;height:26px;border:3px solid var(--ink)}
.brand-name{font-family:'Michroma',sans-serif;font-size:15px;letter-spacing:2px;line-height:1.3;text-transform:uppercase}
.nav a{position:absolute;top:57px;font-size:15px;color:var(--ink);text-decoration:none}
.btn-dark{position:absolute;background:var(--ink);color:var(--white);font-family:'Michroma',sans-serif;text-transform:uppercase;display:flex;align-items:center;justify-content:center;letter-spacing:2px;border-radius:16px 0 16px 0}

/* hero */
.hero-bg{left:0;top:0;width:1200px;height:855px;background:linear-gradient(180deg,#ffffff 0%,#ffffff 22%,#dfe4ea 60%,#b7c1cc 100%)}
.hero-title{left:0;width:1200px;top:160px;text-align:center;font-size:50px;line-height:74px;letter-spacing:10px}
.collage{left:154px;top:416px;width:890px;height:570px;background:var(--white);box-shadow:0 8px 24px rgba(0,0,0,.12)}

/* about */
.section-title{font-size:30px;letter-spacing:8px}
.about-copy{left:453px;width:640px;font-size:15px;line-height:34px;color:var(--muted)}

/* services */
.band{left:0;top:1953px;width:1200px;height:665px;background:var(--band)}
.card{position:absolute;top:2130px;width:305px;border-radius:15px;overflow:hidden}
.card-label{position:absolute;width:265px;white-space:nowrap;font-family:'Michroma',sans-serif;font-size:12.5px;line-height:26px;letter-spacing:1.5px;color:var(--white);text-transform:uppercase}
.card-body{position:absolute;width:260px;font-size:14.5px;line-height:26px;color:#e4e4e4}
.link-u{font-family:'Michroma',sans-serif;font-size:12px;letter-spacing:2px;text-decoration:underline;text-transform:uppercase}

/* capabilities */
.cap-item{left:625px;display:flex;align-items:center;gap:8px;font-family:'Michroma',sans-serif;font-size:19px;letter-spacing:4px;text-transform:uppercase}
.cap-dot{width:14px;height:14px;border:3px solid var(--ink);border-radius:50%}
.rule{left:625px;width:453px;height:1px;background:var(--line)}

/* newsletter + footer */
.footer{left:0;top:3588px;width:1200px;height:381px;background:var(--dark)}
.newsletter{left:132px;top:3350px;width:943px;height:263px;background:var(--white);box-shadow:0 6px 24px rgba(0,0,0,.08)}
.email-input{left:179px;top:3476px;width:620px;height:55px;background:var(--input);font-size:15px;line-height:55px;padding-left:46px;color:#333}
.icon-circle{position:absolute;width:40px;height:40px;border-radius:50%;background:#2b2b2b;display:flex;align-items:center;justify-content:center}
.foot-text{position:absolute;color:var(--white);font-size:13px;line-height:20px}
.social{position:absolute;width:28px;height:28px;border-radius:50%;border:1px solid #bdbdbd}
</style>
</head>
<body>

<!-- hero -->
<div class="abs hero-bg" role="img" aria-label="Bright modern interior with kitchen counter and large windows, softly faded"></div>

<header>
  <div class="abs brand"><span class="brand-mark"></span><span class="brand-name">Northfield<br>Router Works</span></div>
  <nav class="nav">
    <a style="left:394px">Home</a>
    <a style="left:476px">Services We offer</a>
    <a style="left:636px">Capabilities</a>
    <a style="left:758px">About Us</a>
    <a style="left:861px">Contact</a>
  </nav>
  <div class="btn-dark" style="left:962px;top:43px;width:124px;height:45px;font-size:11px;gap:8px">
    <svg width="12" height="12" viewBox="0 0 12 12"><circle cx="6" cy="3.5" r="2.8" fill="#fff"/><path d="M0.5 12c0-3.4 2.5-5 5.5-5s5.5 1.6 5.5 5z" fill="#fff"/></svg>Login
  </div>
</header>

<h1 class="abs display hero-title">Welcome to<br>Northfield Router</h1>
<div class="btn-dark" style="left:511px;top:320px;width:179px;height:43px;font-size:12px">Get Started</div>

<div class="abs collage"></div>
<div class="photo" style="left:160px;top:424px;width:260px;height:269px;background:linear-gradient(160deg,#3a2e25,#7a5a3e 60%,#a07850)" role="img" aria-label="Walk-in closet with lit shelving and wood floor"></div>
<div class="photo" style="left:436px;top:424px;width:604px;height:269px;background:linear-gradient(160deg,#2f2b28,#7d6650 55%,#9a8f85)" role="img" aria-label="Boutique dressing room with wooden shelving and island"></div>
<div class="photo" style="left:160px;top:710px;width:604px;height:269px;background:linear-gradient(160deg,#3b2a22,#9a5a3a 55%,#4a3526)" role="img" aria-label="Warm clothing store with wooden counter and racks"></div>
<div class="photo" style="left:778px;top:710px;width:262px;height:269px;background:linear-gradient(160deg,#2a2624,#6c5a4c 55%,#8f7d6c)" role="img" aria-label="Closet system with drawers and hanging rail"></div>

<!-- about -->
<h2 class="abs display section-title" style="left:114px;top:1068px">About Us</h2>
<div class="btn-dark" style="left:111px;top:1135px;width:200px;height:48px;font-size:13px">Learn More</div>
<p class="abs about-copy" style="top:1060px">Lorem ipsum dolor sit amet, consectetur adipiscing elit, sed do eiusmod tempor incididunt ut labore et dolore magna aliqua. Quis ipsum suspendisse ultrices gravida. Risus commodo viverra maecenas accumsan lacus vel facilisis.</p>
<p class="abs about-copy" style="top:1197px">Lorem ipsum dolor sit amet, consectetur adipiscing elit, sed do eiusmod tempor incididunt ut labore et dolore magna aliqua. Quis ipsum suspendisse ultrices gravida. Risus commodo viverra maecenas accumsan lacus vel facilisis.</p>

<div class="abs" style="left:499px;top:1400px;width:400px;height:396px;border:4px solid var(--frame)"></div>
<div class="photo" style="left:139px;top:1349px;width:639px;height:399px;background:linear-gradient(120deg,#6e4a32,#a67a55 45%,#8a6a50)" role="img" aria-label="Craftsman shaping wood in a workshop"></div>
<div class="photo" style="left:638px;top:1460px;width:425px;height:400px;background:linear-gradient(180deg,#e8e4da,#cfc8b8 60%,#a99a80)" role="img" aria-label="Cream shaker kitchen cabinets with glass doors"></div>

<!-- services -->
<div class="abs band"></div>
<h2 class="abs display" style="left:0;width:1200px;top:2042px;text-align:center;font-size:25px;letter-spacing:8px">Services We Offer</h2>

<div class="card" style="left:111px;height:397px;background:linear-gradient(170deg,#3d342e,#8a7560 50%,#2c2622)" role="img" aria-label="Hand drafting plans beside a building model"></div>
<div class="card-label" style="left:134px;top:2441px">Design Engineering<br>Services</div>

<div class="card" style="left:445px;height:402px;background:#262626"></div>
<div class="abs" style="left:469px;top:2162px;width:50px;height:50px;border-radius:50%;background:var(--white)"></div>
<div class="card-label" style="left:475px;top:2236px">Product<br>Development<br>Prototype Services</div>
<p class="card-body" style="left:475px;top:2332px">Lorem ipsum dolor sit amet, consectetur adipiscing elit, sed do eiusmod tempor incididunt ut labore et dolore magna aliqua. Quis ipsum suspendisse ultrices gravida.</p>
<div class="abs link-u" style="left:475px;top:2482px;color:var(--white)">Learn More</div>

<div class="card" style="left:782px;height:397px;background:linear-gradient(160deg,#7a8a9a,#2a2a2a 55%,#55606a)" role="img" aria-label="3D printer at work"></div>
<div class="card-label" style="left:806px;top:2471px">3D Printer Farm</div>

<!-- capabilities -->
<div class="photo" style="left:111px;top:2716px;width:229px;height:444px;border-radius:8px;background:linear-gradient(170deg,#2c2a28,#6a6055 55%,#c9c2b6)" role="img" aria-label="Glass-front wardrobe with hanging clothes"></div>
<div class="photo" style="left:354px;top:2800px;width:230px;height:443px;border-radius:8px;background:linear-gradient(170deg,#b06a42,#2f3a30 45%,#6a4030)" role="img" aria-label="Row of green lockers with copper handles"></div>

<h2 class="abs display" style="left:628px;top:2760px;font-size:27px;letter-spacing:6px">Capabilities</h2>
<div class="abs cap-item" style="top:2833px"><span class="cap-dot"></span>Cabinet Shops</div>
<p class="abs" style="left:647px;top:2870px;width:450px;font-size:14px;line-height:30px;color:var(--muted)">Lorem ipsum dolor sit amet, consectetur adipiscing elit, sed do eiusmod tempor incididunt ut labore et dolore magna aliqua. Quis ipsum suspendisse ultrices gravida. Risus commodo viverra maecenas accumsan lacus vel facilisis.</p>
<div class="abs link-u" style="left:648px;top:3001px">Learn More</div>
<div class="abs rule" style="top:3052px"></div>
<div class="abs cap-item" style="top:3078px"><span class="cap-dot"></span>Builders</div>
<div class="abs rule" style="top:3145px"></div>
<div class="abs cap-item" style="top:3170px"><span class="cap-dot"></span>Closet Companies</div>

<!-- footer -->
<div class="abs footer"></div>
<div class="abs newsletter"></div>
<h2 class="abs display" style="left:132px;width:943px;top:3402px;text-align:center;font-size:25px;letter-spacing:8px">Sign Up Our Newsletter</h2>
<div class="abs email-input">Enter Your Email</div>
<div class="abs" style="left:799px;top:3476px;width:227px;height:55px;background:var(--ink);color:var(--white);font-family:'Michroma',sans-serif;font-size:11px;letter-spacing:2px;text-transform:uppercase;display:flex;align-items:center;justify-content:center">Subscribe</div>

<div class="abs" style="left:143px;top:3700px;display:flex;align-items:center;gap:14px">
  <span style="width:34px;height:34px;border:3px solid var(--white)"></span>
  <span style="font-family:'Michroma',sans-serif;font-size:20px;letter-spacing:3px;color:var(--white);line-height:1.3;text-transform:uppercase">Northfield<br>Router Works</span>
</div>

<div class="icon-circle" style="left:488px;top:3688px"><svg width="14" height="18" viewBox="0 0 14 18"><path d="M7 0C3.1 0 0 3 0 6.8 0 11.9 7 18 7 18s7-6.1 7-11.2C14 3 10.9 0 7 0z" fill="#fff"/><circle cx="7" cy="6.8" r="2.4" fill="#2b2b2b"/></svg></div>
<div class="foot-text" style="left:544px;top:3690px">42 Mill Street, Suite B<br>Lakeview, MN 55000</div>
<div class="icon-circle" style="left:750px;top:3690px"><svg width="16" height="16" viewBox="0 0 16 16"><path d="M3.2 0.8l2.4 0 1.2 3.6-1.8 1.2c.9 2 2.4 3.5 4.4 4.4l1.2-1.8 3.6 1.2 0 2.4c0 1.2-1 2.2-2.2 2.2C6 14 2 10 2 3 2 1.8 2 .8 3.2.8z" fill="#fff"/></svg></div>
<div class="foot-text" style="left:810px;top:3700px">Phone<br>+1 555 010 2040</div>
<div class="icon-circle" style="left:488px;top:3758px"><svg width="16" height="12" viewBox="0 0 16 12"><rect width="16" height="12" rx="1.5" fill="#fff"/><path d="M1 1.5l7 5 7-5" stroke="#2b2b2b" stroke-width="1.5" fill="none"/></svg></div>
<div class="foot-text" style="left:538px;top:3763px">Email<br>hello@northfieldrouter.example</div>

<span class="social" style="left:992px;top:3693px"></span>
<span class="social" style="left:1029px;top:3693px"></span>
<span class="social" style="left:992px;top:3730px"></span>
<span class="social" style="left:1029px;top:3730px"></span>

<div class="abs" style="left:111px;top:3855px;width:976px;height:1px;background:#3a3a3a"></div>
<div class="abs" style="left:0;width:1200px;top:3900px;text-align:center;font-family:'Michroma',sans-serif;font-size:12px;letter-spacing:2px;color:var(--white);text-transform:uppercase">©Copyrights 2023 Northfield Router Works &nbsp; | &nbsp; All Rights Reserved</div>

</body>
</html>
```